Life Coaching business needs a new flyer

We are an Australian business that specialises in Life Coaching, Career Coaching, Health and Wellness Coaching, Yoga and Pilates. We need a A4 double sided flyer that is full colour and folded to DL format. I have attached a couple of designs that I like and some pictures and would like the flyer to be bright yet stylish.

Industry/Entity Type

Life Coaching

```html
<!DOCTYPE html>
<html lang="en">
<head>
<meta charset="utf-8">
<title>Life Coaching Trifold Flyer</title>
<link href="https://fonts.googleapis.com/css2?family=Open+Sans:wght@400;600;700&family=PT+Serif:wght@400;700&family=Great+Vibes&display=swap" rel="stylesheet">
<style>
:root{
  --blue:#2467b0;
  --blue-dark:#15457f;
  --blue-light:#5aa0dc;
  --green:#4aa648;
  --ink:#2d2d2d;
  --muted:#555;
  --paper:#ffffff;
  --bg:#ffffff;
}
*{margin:0;padding:0;box-sizing:border-box}
html,body{width:874px;height:1200px;overflow:hidden;background:var(--bg)}
body{font-family:"Open Sans",sans-serif;color:var(--ink);position:relative}
.sheet{position:absolute;left:15px;width:845px;display:flex;box-shadow:0 3px 10px rgba(0,0,0,.25)}
.sheet--outside{top:30px;height:564px}
.sheet--inside{top:624px;height:562px;background:var(--paper)}
.panel{width:33.333%;position:relative;overflow:hidden}
.photo{position:absolute}

/* outside */
.testimonials{background:linear-gradient(180deg,var(--blue-dark),var(--blue) 55%,var(--blue-light));color:#fff;padding:16px 16px}
.testimonials h2{font-family:"PT Serif",serif;font-size:21px;font-weight:700;margin-bottom:10px;line-height:1.2}
.testimonials p{font-size:9.4px;line-height:1.5;margin-bottom:9px;position:relative;z-index:1}
.testimonials .photo{left:0;right:0;bottom:0;height:130px;background:linear-gradient(180deg,rgba(90,160,220,0),#7e9bb4 40%,#a88c74)}
.offer{background:var(--paper)}
.offer .photo{left:0;top:0;width:100%;height:230px;background:linear-gradient(135deg,#c9b6a2,#8c7563 60%,#5e4a3d)}
.offer__text{position:absolute;top:230px;left:0;right:0;height:80px;text-align:center;padding-top:12px;font-size:10.5px;font-weight:700;line-height:1.45;color:var(--ink)}
.offer__text small{display:block;font-weight:600;font-size:9.5px}
.contact{position:absolute;top:310px;left:0;right:0;bottom:0;background:linear-gradient(180deg,var(--blue),var(--blue-dark));color:#fff;padding:24px 20px}
.contact h3{font-family:"PT Serif",serif;font-size:22px;font-weight:400;text-align:center;margin-bottom:22px}
.contact li{list-style:none;display:flex;align-items:center;gap:9px;font-size:9.5px;margin-bottom:18px}
.contact svg{flex:none}
.cover{background:linear-gradient(180deg,#eaf4fb,#ffffff 40%)}
.brand{position:absolute;top:48px;left:0;right:0;display:flex;align-items:center;justify-content:center;gap:8px}
.brand__dot{width:12px;height:12px;border-radius:50%;background:var(--green)}
.brand__name{font-family:"PT Serif",serif;font-size:20px;font-weight:700;color:var(--green)}
.cover__title{position:absolute;top:100px;left:0;right:0;text-align:center;font-family:"Great Vibes",cursive;font-size:34px;line-height:1.08;color:var(--blue)}
.cover .photo{left:0;right:0;bottom:0;height:330px;background:linear-gradient(180deg,#e6f1f9,#a9cdea 35%,#6ea1cf 70%,#4f86b8)}

/* inside */
.inside{padding:14px 16px 0;font-size:8.8px;line-height:1.5;color:var(--muted)}
.inside h4{font-family:"PT Serif",serif;color:var(--blue);font-size:14px;font-weight:700;margin:8px 0 4px;line-height:1.25}
.inside p{margin-bottom:7px}
.q{font-weight:700;color:var(--ink);font-size:9.4px;margin-bottom:11px}
.need{display:flex;align-items:center;gap:8px;margin-bottom:7px}
.need h4{margin:0}
.checks{margin-bottom:4px}
.checks li{list-style:none;display:flex;gap:6px;align-items:center;margin-bottom:3px}
.strip{position:absolute;left:0;right:0;bottom:0;height:62px;display:flex}
.strip div{flex:1}
</style>
</head>
<body>

<section class="sheet sheet--outside">
  <div class="panel testimonials">
    <h2>Happy Clients Testimonials</h2>
    <p>"Coaching gave me the clarity and confidence to change my career. I now wake up excited about my work and my future every single day, and I finally feel like I am heading in the right direction."</p>
    <p>"I was stuck for years before these sessions. The gentle guidance helped me set goals, build habits and finally move forward with real purpose."</p>
    <p>"The yoga classes are calm and welcoming. My stress has dropped, my sleep has improved and I feel far more balanced at home and at work."</p>
    <p>"I had no idea how much one hour a week could change. My relationships, focus and energy have all grown since I started coaching."</p>
    <p>"Meditation has become part of my daily routine. I am calmer, kinder to myself and better able to handle whatever the week brings."</p>
    <div class="photo" role="img" aria-label="Photo of smiling happy clients together outdoors"></div>
  </div>

  <div class="panel offer">
    <div class="photo" role="img" aria-label="Photo of two women coaches smiling"></div>
    <div class="offer__text">Free Introductory Life Coaching<br>Phone/Skype session - 30 mins<small>(To see if coaching is right for you)</small></div>
    <div class="contact">
      <h3>contact us</h3>
      <ul>
        <li><svg width="16" height="16" viewBox="0 0 24 24"><path fill="#fff" d="M6.6 10.8a15 15 0 006.6 6.6l2.2-2.2c.3-.3.7-.4 1-.2 1.1.4 2.3.6 3.6.6.6 0 1 .4 1 1V20c0 .6-.4 1-1 1A17 17 0 013 4c0-.6.4-1 1-1h3.5c.6 0 1 .4 1 1 0 1.3.2 2.5.6 3.6.1.3 0 .7-.2 1z"/></svg>0400 123 456</li>
        <li><svg width="16" height="16" viewBox="0 0 24 24"><rect x="2" y="5" width="20" height="14" rx="2" fill="none" stroke="#fff" stroke-width="2"/><path d="M2 6l10 7 10-7" fill="none" stroke="#fff" stroke-width="2"/></svg>hello@brightpathcoaching.com.au</li>
        <li><svg width="16" height="16" viewBox="0 0 24 24"><circle cx="12" cy="12" r="9" fill="none" stroke="#fff" stroke-width="2"/><path d="M3 12h18M12 3c3 3 3 15 0 18M12 3c-3 3-3 15 0 18" fill="none" stroke="#fff" stroke-width="1.6"/></svg>brightpathcoaching.com.au</li>
      </ul>
    </div>
  </div>

  <div class="panel cover">
    <div class="brand"><span class="brand__dot"></span><span class="brand__name">BrightPath Coaching</span></div>
    <div class="cover__title">Life Coaching<br>Meditation<br>Yoga/Pilates</div>
    <div class="photo" role="img" aria-label="Photo of people doing yoga poses against the sky"></div>
  </div>
</section>

<section class="sheet sheet--inside">
  <div class="panel inside">
    <p class="q">Are you looking or making changes this year?</p>
    <p class="q">Are you stuck in a rut or at a crossroad in your life?</p>
    <p class="q">Are you wanting to lose weight but can't get motivated?</p>
    <p class="q">Do you have ongoing problems with your career, relationships, or just life itself?</p>
    <p class="q">Life coaching is the answer.</p>
    <h4>Life Coaching and Meditation Centre of Excellence</h4>
    <p>Our mission is to help you become the best possible person you can be, mentally, physically and spiritually.</p>
    <p>We offer highly qualified and compassionate trainers for Life Coaching, Meditation, Yoga and Pilates.</p>
    <p>They will guide and motivate you every step of the way to achieve all your dreams and goals.</p>
    <p>They will make you the best you can be.</p>
  </div>

  <div class="panel inside">
    <h4 style="margin-top:0">Life Coaching</h4>
    <p>Your Life Coach will give you the confidence and the ability to move forward in a positive manner in all areas of your life where you want change.</p>
    <p>Life Coaching is about looking at the barriers preventing change, from your past, and creating the ideal environment for positive action to take place. It is a holistic approach that helps you focus on what matters most.</p>
    <h4>Career Coaching</h4>
    <p>Are you at a crossroad in your career and at a loss about what to do next? Do you want to be aligned with the right path? Our coaches explore your skills, strengths and values, and give you the confidence to take your next step. With the right support you will set clear goals and build a career that feels rewarding.</p>
    <h4>Wellness Coaching</h4>
    <p>Health and wellness coaching looks at nutrition, movement, sleep and stress. We work alongside you to build lasting habits and a balanced lifestyle that supports the future you want.</p>
  </div>

  <div class="panel inside">
    <div class="need">
      <svg width="22" height="22" viewBox="0 0 24 24"><circle cx="12" cy="12" r="11" fill="var(--green)"/><path d="M9 9a3 3 0 116 .5c0 2-3 2-3 4M12 17v.5" stroke="#fff" stroke-width="2" fill="none" stroke-linecap="round"/></svg>
      <h4>Why Would I Need Help?</h4>
    </div>
    <p>Coaching is the answer when you want to make lasting changes in your life.</p>
    <p>Coaching can assist with such issues as:</p>
    <ul class="checks">
      <li><svg width="9" height="9" viewBox="0 0 10 10"><path d="M1 5l3 3 5-7" stroke="var(--green)" stroke-width="2" fill="none"/></svg>Creating a better work-life balance</li>
      <li><svg width="9" height="9" viewBox="0 0 10 10"><path d="M1 5l3 3 5-7" stroke="var(--green)" stroke-width="2" fill="none"/></svg>Resolving relationship issues</li>
      <li><svg width="9" height="9" viewBox="0 0 10 10"><path d="M1 5l3 3 5-7" stroke="var(--green)" stroke-width="2" fill="none"/></svg>Career guidance</li>
      <li><svg width="9" height="9" viewBox="0 0 10 10"><path d="M1 5l3 3 5-7" stroke="var(--green)" stroke-width="2" fill="none"/></svg>Stress management</li>
      <li><svg width="9" height="9" viewBox="0 0 10 10"><path d="M1 5l3 3 5-7" stroke="var(--green)" stroke-width="2" fill="none"/></svg>Weight loss and fitness</li>
      <li><svg width="9" height="9" viewBox="0 0 10 10"><path d="M1 5l3 3 5-7" stroke="var(--green)" stroke-width="2" fill="none"/></svg>Motivation and goal setting</li>
      <li><svg width="9" height="9" viewBox="0 0 10 10"><path d="M1 5l3 3 5-7" stroke="var(--green)" stroke-width="2" fill="none"/></svg>Boosting self-confidence</li>
      <li><svg width="9" height="9" viewBox="0 0 10 10"><path d="M1 5l3 3 5-7" stroke="var(--green)" stroke-width="2" fill="none"/></svg>Overcoming negative thoughts</li>
    </ul>
    <h4>Meditation</h4>
    <p>We specialise in teaching meditation from beginners to advanced, with a variety of techniques for calm, relaxation and peace of mind in daily life.</p>
    <h4>Yoga/Pilates</h4>
    <p>Our highly qualified and experienced Yoga and Pilates trainers will come to you and create a fun and varied workout based on what you enjoy and what your goals are.</p>
  </div>

  <div class="strip" role="img" aria-label="Strip of photos showing coaching, meditation and yoga sessions">
    <div style="background:linear-gradient(90deg,#b59c84,#8fb0c9)"></div>
    <div style="background:linear-gradient(90deg,#8fb0c9,#c7d9e6)"></div>
    <div style="background:linear-gradient(90deg,#c7d9e6,#7fa6c6)"></div>
  </div>
</section>

</body>
</html>
```